Specialised investor in e-mobility and energy wants business card design

We need a business card design that fits our existing corporate design. <The look and feel must be 'sharp'/'clean', dynamic, communicate momentum, professionalism etc (as one would imagine from a firm in the financial sector). We like the idea of a reverse-side of the card that includes the logo, and the name and contact details on the other. We expect the deliverable to be whatever format might be required to be able to get cards printed directly by a service such as kelmo press. Our website is www.zub.capital

```html
<!DOCTYPE html>
<html lang="en">
<head>
<meta charset="utf-8">
<title>ZUB Capital – Business Card</title>
<link href="https://fonts.googleapis.com/css2?family=Montserrat:wght@400;500;700&display=swap" rel="stylesheet">
<style>
  :root {
    --green-dark: #344f24;
    --green-light: #86b049;
    --ink: #2e2e2e;
    --paper: #ffffff;
    --stage: #2b2b2b;
    --watermark: #eeefeb;
  }
  * { margin: 0; padding: 0; box-sizing: border-box; }
  html, body { width: 1200px; height: 1059px; overflow: hidden; }
  body {
    background: var(--stage);
    font-family: "Montserrat", Arial, sans-serif;
    position: relative;
  }
  .card {
    position: absolute;
    border-radius: 22px;
    overflow: hidden;
  }
  .card-front {
    left: 257px; top: 89px; width: 687px; height: 390px;
    background: var(--paper);
    color: var(--ink);
  }
  .card-back {
    left: 254px; top: 547px; width: 693px; height: 394px;
    background: var(--green-dark);
  }
  .watermark {
    position: absolute; left: 32px; top: 30px;
    font-size: 128px; font-weight: 700; letter-spacing: 2px;
    color: var(--watermark); line-height: 1;
  }
  .wordmark {
    position: absolute;
    font-weight: 500;
    white-space: nowrap;
    line-height: 1;
  }
  .card-front .wordmark {
    right: 38px; top: 64px;
    font-size: 50px; color: var(--green-dark);
  }
  .card-back .wordmark {
    left: 0; right: 0; top: 152px; text-align: center;
    font-size: 86px; color: var(--paper);
  }
  .holder { position: absolute; left: 42px; top: 200px; }
  .holder-name {
    font-size: 26px; font-weight: 700; letter-spacing: 1.5px;
    color: var(--green-dark); line-height: 1.1;
  }
  .holder-name .surname { color: var(--green-light); }
  .holder-role { font-size: 15px; letter-spacing: .5px; margin-top: 2px; }
  .divider {
    position: absolute; left: 42px; right: 38px; top: 262px;
    height: 1px; background: var(--green-dark);
  }
  .contacts {
    position: absolute; left: 42px; top: 280px;
    list-style: none; font-size: 16px; letter-spacing: .5px;
  }
  .contacts li { display: flex; align-items: center; height: 27px; }
  .contacts svg { width: 12px; height: 12px; margin-right: 7px; fill: var(--green-light); }
  .address {
    position: absolute; right: 38px; top: 312px;
    text-align: right; font-size: 16px; letter-spacing: .5px; line-height: 22px;
    font-style: normal;
  }
  .edge-band {
    position: absolute; left: 0; bottom: 0; width: 100%; height: 9px;
  }
</style>
</head>
<body>
  <section class="card card-front">
    <div class="watermark" aria-hidden="true">ZUB</div>
    <div class="wordmark">ZUB Capital</div>

    <div class="holder">
      <div class="holder-name">MARTEN <span class="surname">KOVEL</span></div>
      <div class="holder-role">Director/Founder</div>
    </div>

    <div class="divider"></div>

    <ul class="contacts">
      <li>
        <svg viewBox="0 0 24 24" aria-hidden="true"><path d="M6.6 10.8a15.1 15.1 0 0 0 6.6 6.6l2.2-2.2a1 1 0 0 1 1-.25 11.4 11.4 0 0 0 3.6.57 1 1 0 0 1 1 1V20a1 1 0 0 1-1 1A17 17 0 0 1 3 4a1 1 0 0 1 1-1h3.5a1 1 0 0 1 1 1c0 1.25.2 2.45.57 3.57a1 1 0 0 1-.25 1z"/></svg>
        123-480-2917
      </li>
      <li>
        <svg viewBox="0 0 24 24" aria-hidden="true"><path d="M2 5h20v14H2z M2 5l10 8 10-8" /></svg>
        info@zub.capital
      </li>
      <li>
        <svg viewBox="0 0 24 24" aria-hidden="true"><circle cx="12" cy="12" r="11"/></svg>
        www.zub.capital
      </li>
    </ul>

    <address class="address">
      1234 Street Name<br>
      Country Name AB 5748
    </address>

    <svg class="edge-band" viewBox="0 0 687 9" preserveAspectRatio="none" aria-hidden="true">
      <polygon points="0,0 337,0 328,9 0,9" fill="var(--green-dark)"/>
      <polygon points="345,0 687,0 687,9 336,9" fill="var(--green-light)"/>
    </svg>
  </section>

  <section class="card card-back">
    <div class="wordmark">ZUB Capital</div>
  </section>
</body>
</html>
```